Business cards to launch an education platform

Hi,
I am looking at having new business cards designed.
I am a startup, developing a web platform for schools and university, the education world. It's an online assessment system.
I would like a card that looks classy, and that is using the colors and the font of my logo.

I have attached:
1) my logo
2) A business card that I have designed quickly so you can have all the information required in the card, but I really don't like it.
3) The font that I am using (Lato Regular) to design my web platform
4) Some screenshots of my web platform so you can have a look at the style that I have.

Target Market(s)

Major market: Education system: Schools and university
Minor markets: Business in general

Industry/Entity Type

Business

Contact Information for Business Card

Clara Fenwick
Director

M: 0437 518 902
E: clara.fenwick@amberLoomSystems.com.au

Requirements
Must have
• The colors of my logo

```html
<!DOCTYPE html>
<html lang="en">
<head>
<meta charset="utf-8">
<title>Amber Loom Systems – Business Cards</title>
<link rel="stylesheet" href="https://fonts.googleapis.com/css2?family=Lato:wght@400;700&display=swap">
<style>
  :root {
    --page-bg: #8f9092;
    --card-light: #ececee;
    --navy: #093766;
    --sapphire: #1b8fd4;
    --ink: #3a3b40;
    --white: #ffffff;
  }
  * { margin: 0; padding: 0; box-sizing: border-box; }
  html, body {
    width: 1105px;
    height: 1200px;
    overflow: hidden;
    background: var(--page-bg);
    font-family: "Lato", sans-serif;
  }
  .canvas {
    position: relative;
    width: 1105px;
    height: 1200px;
  }
  .card {
    position: absolute;
    left: 179px;
    width: 747px;
    height: 425px;
    overflow: hidden;
  }

  /* Front */
  .card--front {
    top: 120px;
    background: var(--card-light);
  }
  .name-band {
    position: absolute;
    left: 0;
    top: 60px;
    width: 430px;
    height: 115px;
    background: var(--navy);
    color: var(--white);
    padding: 30px 0 0 51px;
  }
  .name-band__name {
    font-size: 25px;
    font-weight: 700;
    letter-spacing: 0.3px;
    text-transform: uppercase;
    line-height: 1.15;
  }
  .name-band__title {
    font-size: 19px;
    font-weight: 400;
    text-transform: uppercase;
    line-height: 1.3;
  }
  .brand {
    position: absolute;
    left: 455px;
    top: 80px;
    display: flex;
    align-items: center;
    gap: 16px;
  }
  .brand__mark {
    width: 66px;
    height: 66px;
    background: var(--sapphire);
  }
  .brand__name {
    color: var(--navy);
    font-size: 30px;
    font-weight: 400;
    letter-spacing: 1.5px;
    line-height: 1.1;
  }
  .contact {
    position: absolute;
    left: 0;
    right: 0;
    top: 330px;
    text-align: center;
    color: var(--ink);
    transform: translateX(17px);
  }
  .contact__phone {
    font-size: 19px;
    font-weight: 700;
    line-height: 1.45;
  }
  .contact__email {
    font-size: 19px;
    font-weight: 400;
    line-height: 1.45;
  }

  /* Back */
  .card--back {
    top: 637px;
    background: var(--navy);
    color: var(--white);
  }
  .back-brand {
    position: absolute;
    left: 57px;
    top: 275px;
  }
  .back-brand__name {
    font-size: 42px;
    font-weight: 400;
    letter-spacing: 4px;
    line-height: 1.1;
  }
  .back-brand__url {
    margin-top: 10px;
    font-size: 19px;
    font-weight: 400;
  }
</style>
</head>
<body>
<main class="canvas">

  <section class="card card--front" aria-label="Business card front">
    <div class="name-band">
      <p class="name-band__name">Clara Fenwick</p>
      <p class="name-band__title">Director</p>
    </div>
    <div class="brand">
      <span class="brand__mark" aria-hidden="true"></span>
      <p class="brand__name">AMBER LOOM<br>SYSTEMS</p>
    </div>
    <div class="contact">
      <p class="contact__phone">0437 518 902</p>
      <p class="contact__email">clara.fenwick@amberLoomSystems.com.au</p>
    </div>
  </section>

  <section class="card card--back" aria-label="Business card back">
    <div class="back-brand">
      <p class="back-brand__name">AMBER LOOM<br>SYSTEMS</p>
      <p class="back-brand__url">amberLoomSystems.com.au</p>
    </div>
  </section>

</main>
</body>
</html>
```